Need to drive pregnant women to my 3d4d ultrasound studio where i provide 4d ultrasound with hyperalistic imaging and gender reveals

Industry/Entity Type

Healthcare

Font styles to use
Decorative
Script

Requirements
Must have
• My Company name Cielo de Nuestra Espera 4D. EVERYTHING HAS TO BE IN SPANISH
Nice to have
• SIMPLE AND NOT TOO BUSY
Should not have
• website

```html
<!DOCTYPE html>
<html lang="es">
<head>
<meta charset="utf-8">
<title>Cielo de Nuestra Espera 4D</title>
<link rel="stylesheet" href="https://fonts.googleapis.com/css2?family=Roboto:wght@500;700;900&display=swap">
<style>
  :root {
    --backdrop: #a1a1a1;
    --paper: #ffffff;
    --ink: #000000;
    --ink-reverse: #ffffff;
    --scan-light: #c97a2a;
    --scan-dark: #3a1a06;
    --skin-light: #f3cdbd;
    --skin-dark: #b07a68;
  }
  * { margin: 0; padding: 0; box-sizing: border-box; }
  html, body {
    width: 1200px;
    height: 600px;
    overflow: hidden;
    background: var(--backdrop);
    font-family: "Roboto", Arial, sans-serif;
  }
  .banner {
    position: absolute;
    left: 30px;
    top: 134px;
    width: 1140px;
    height: 332px;
    background: var(--paper);
    overflow: hidden;
  }
  .banner__band {
    position: absolute;
    left: 0;
    top: 106px;
    width: 100%;
    height: 134px;
    background: var(--ink);
  }
  .banner__title-top {
    position: absolute;
    left: 48px;
    top: 42px;
    font-size: 62px;
    font-weight: 500;
    line-height: 1;
    color: var(--ink);
    letter-spacing: 0.5px;
    white-space: nowrap;
  }
  .banner__title-main {
    position: absolute;
    left: 44px;
    top: 111px;
    font-size: 126px;
    font-weight: 700;
    line-height: 1;
    color: var(--ink-reverse);
    letter-spacing: 1px;
    white-space: nowrap;
  }
  .banner__tagline {
    position: absolute;
    left: 50px;
    top: 263px;
    font-size: 18.5px;
    font-weight: 500;
    color: var(--ink);
    white-space: nowrap;
  }
  .gallery {
    position: absolute;
    left: 716px;
    top: 41px;
    width: 388px;
    height: 256px;
    background: var(--ink);
    padding: 5px;
    display: flex;
    gap: 5px;
  }
  .gallery__photo {
    flex: 1;
    height: 100%;
  }
  .gallery__photo--scan {
    background: radial-gradient(ellipse at 45% 55%, var(--scan-light) 0%, #8a4712 55%, var(--scan-dark) 100%);
  }
  .gallery__photo--newborn {
    background: radial-gradient(ellipse at 45% 60%, var(--skin-light) 0%, #dca594 55%, var(--skin-dark) 100%);
  }
</style>
</head>
<body>
  <section class="banner">
    <div class="banner__band"></div>
    <h1>
      <span class="banner__title-top">CIELO DE NUESTRA</span>
      <span class="banner__title-main">ESPERA 4D</span>
    </h1>
    <p class="banner__tagline">Ultrasonido 4D con imágenes hiperrealistas y revelación de género</p>
    <div class="gallery">
      <div class="gallery__photo gallery__photo--scan" role="img" aria-label="Imagen de ultrasonido 4D de un bebé en tonos ámbar"></div>
      <div class="gallery__photo gallery__photo--newborn" role="img" aria-label="Fotografía de un recién nacido dormido"></div>
    </div>
  </section>
</body>
</html>
```